Halberd Guard Services

Our Company is a security business which needs a cut edge design, the final product should have all relevant information and maintain a bold but modern and professional look.

Target Market(s)

A cut edge design which will attract any audience

Industry/Entity Type

Security

Contact Information for Business Card

HALBERD GUARD SERVICES

Gregor Lindqvist
Operations Manager
Phone: 0491 735 219

Email: info@halberdguard.com.au
Web: www.halberdguard.com.au

Requirements
Must have
• Must be double sided and contain all relevant information and the company logo.

```html
<!DOCTYPE html>
<html lang="en">
<head>
<meta charset="utf-8">
<title>Halberd Guard Services – Business Card</title>
<link href="https://fonts.googleapis.com/css2?family=Open+Sans:wght@400;600;700;800&display=swap" rel="stylesheet">
<style>
  :root {
    --stage: #e9e7e3;
    --card: #ffffff;
    --ink: #1c1c1c;
    --brand: #3a5560;
    --accent: #f39a1e;
    --accent-deep: #e07d10;
    --rule: #c9ced1;
    --band-line: #2f3b40;
  }
  * { box-sizing: border-box; margin: 0; padding: 0; }
  html, body {
    width: 1200px; height: 951px; overflow: hidden;
    background: var(--stage);
    font-family: "Open Sans", Arial, sans-serif;
    color: var(--ink);
  }
  .canvas { position: relative; width: 1200px; height: 951px; }

  .card {
    position: absolute;
    width: 600px; height: 340px;
    background: var(--card);
    border-radius: 22px;
    overflow: hidden;
    box-shadow: 0 10px 28px rgba(0,0,0,.18);
  }
  .card-front { left: 90px; top: 90px; }
  .card-back  { left: 510px; top: 520px; }

  .edge-band {
    position: absolute; left: 0; right: 0; bottom: 0; height: 26px;
    background: linear-gradient(180deg, var(--accent), var(--accent-deep));
  }
  .card-back .edge-band { border-top: 3px solid var(--band-line); height: 34px; }

  .brand-mark { display: flex; align-items: center; gap: 14px; }
  .brand-mark .dot {
    width: 22px; height: 22px; border-radius: 50%; flex: none;
    background: var(--accent);
  }
  .brand-name {
    font-weight: 800; color: var(--brand);
    letter-spacing: 1px; line-height: 1.1; text-transform: uppercase;
  }

  .card-front .brand-mark {
    position: absolute; left: 20px; right: 20px; top: 112px; justify-content: center;
  }
  .card-front .brand-name { font-size: 30px; white-space: nowrap; }
  .card-front .web {
    position: absolute; left: 0; right: 0; top: 230px; text-align: center;
    font-size: 19px; letter-spacing: 1.5px; color: var(--brand);
  }

  .card-back .brand-block {
    position: absolute; left: 0; top: 0; width: 230px; height: 306px;
    display: flex; align-items: center; justify-content: center;
  }
  .card-back .brand-mark { flex-direction: column; gap: 12px; }
  .card-back .brand-name { font-size: 24px; text-align: center; }
  .divider {
    position: absolute; left: 232px; top: 26px; width: 1px; height: 256px;
    background: var(--rule);
  }
  .details { position: absolute; left: 268px; top: 34px; right: 20px; }
  .person-name { font-size: 21px; font-weight: 600; }
  .person-role { font-size: 15px; color: var(--accent); margin-top: -2px; }
  .address { margin-top: 30px; display: flex; gap: 12px; font-size: 16px; line-height: 1.25; align-items: flex-start; }
  .contacts { margin-top: 20px; list-style: none; font-size: 16px; line-height: 1.35; }
  .contacts li { display: flex; gap: 12px; align-items: center; white-space: nowrap; }
  .icon { width: 16px; height: 16px; flex: none; fill: var(--accent); }
  .address .icon { margin-top: 2px; }
</style>
</head>
<body>
<main class="canvas">

  <section class="card card-front" aria-label="Card front">
    <div class="brand-mark">
      <span class="dot"></span>
      <span class="brand-name">Halberd Guard Services</span>
    </div>
    <p class="web">www.halberdguard.com.au</p>
    <div class="edge-band"></div>
  </section>

  <section class="card card-back" aria-label="Card back">
    <div class="brand-block">
      <div class="brand-mark">
        <span class="dot"></span>
        <span class="brand-name">Halberd<br>Guard<br>Services</span>
      </div>
    </div>
    <div class="divider"></div>

    <div class="details">
      <p class="person-name">Gregor Lindqvist</p>
      <p class="person-role">Operations Manager</p>

      <div class="address">
        <svg class="icon" viewBox="0 0 16 16" aria-hidden="true"><path d="M8 1 1 7.5h2V15h4v-4h2v4h4V7.5h2z"/></svg>
        <span>14 Ridgeline Avenue<br>Marlow NSW 2145</span>
      </div>

      <ul class="contacts">
        <li>
          <svg class="icon" viewBox="0 0 16 16" aria-hidden="true"><path d="M4 1h3l1 4-2 1.2a8 8 0 0 0 3.8 3.8L11 8l4 1v3c0 1.2-1 2-2 2C6.9 14 2 9.1 2 3c0-1 .8-2 2-2z"/></svg>
          <span>0491 735 219</span>
        </li>
        <li>
          <svg class="icon" viewBox="0 0 16 16" aria-hidden="true"><path d="M4 1h8v5H4zM2 7h12v7H2zm2 2v1h2V9zm3 0v1h2V9zm3 0v1h2V9z"/></svg>
          <span>02 9730 4419</span>
        </li>
        <li>
          <svg class="icon" viewBox="0 0 16 16" aria-hidden="true"><path d="M1 3h14v10H1zm1.5 1.5L8 9l5.5-4.5V4h-11z"/></svg>
          <span>info@halberdguard.com.au</span>
        </li>
        <li>
          <svg class="icon" viewBox="0 0 16 16" aria-hidden="true"><circle cx="8" cy="8" r="7"/></svg>
          <span>www.halberdguard.com.au</span>
        </li>
      </ul>
    </div>

    <div class="edge-band"></div>
  </section>

</main>
</body>
</html>
```